Business Card Design

Company is a Commercial Building Company specialising in New Construction and existing refurbishments

Industry/Entity Type

Business

Contact Information for Business Card

Liam Porter
Construction Manager
E Liam@marshbuilding.com.au
M 0400 213 594
Mail 14 Tarrant Rise Harbourvale WA 6299

```html
<!DOCTYPE html>
<html lang="en">
<head>
<meta charset="utf-8">
<title>Marsh Building &amp; Construction — Business Card</title>
<link rel="stylesheet" href="https://fonts.googleapis.com/css2?family=Tinos:wght@400;700&display=swap">
<style>
  :root {
    --page: #e9e6e2;
    --card: #ffffff;
    --orange: #f5a03a;
    --cyan: #12c6df;
    --ink: #111111;
    --brand: #3e4452;
  }
  html, body {
    margin: 0;
    width: 1200px;
    height: 914px;
    overflow: hidden;
    background: var(--page);
    font-family: "Tinos", "Times New Roman", serif;
  }
  .sheet {
    position: relative;
    width: 1200px;
    height: 914px;
  }
  .card {
    position: absolute;
    left: 270px;
    width: 660px;
    height: 377px;
    background: var(--card);
    box-shadow: 0 4px 14px rgba(0,0,0,0.12);
    overflow: hidden;
  }
  .card--back { top: 50px; }
  .card--front { top: 487px; }
  .card__shapes {
    position: absolute;
    inset: 0;
  }
  .brand {
    position: absolute;
    left: 0;
    right: 0;
    text-align: center;
    color: var(--brand);
    font-weight: 700;
    text-transform: uppercase;
    line-height: 1.05;
  }
  .card--back .brand { top: 135px; font-size: 30px; letter-spacing: 1px; }
  .card--front .brand { top: 38px; font-size: 22px; letter-spacing: 1px; }
  .brand__line { display: block; }
  .brand__line--sub { font-size: 0.78em; }
  .person {
    position: absolute;
    top: 120px;
    left: 0;
    right: 0;
    text-align: center;
    color: var(--ink);
  }
  .person__name { font-size: 24px; margin: 0; font-weight: 400; }
  .person__role { font-size: 17px; margin: 2px 0 0; }
  .contacts {
    position: absolute;
    left: 22px;
    top: 224px;
    margin: 0;
    padding: 0;
    list-style: none;
    font-size: 18px;
    color: var(--ink);
  }
  .contacts li {
    display: flex;
    align-items: center;
    gap: 12px;
    margin-bottom: 8px;
  }
  .contacts svg { width: 16px; height: 16px; flex: none; }
  .address {
    position: absolute;
    right: 24px;
    top: 286px;
    display: flex;
    align-items: center;
    gap: 12px;
    font-size: 18px;
    color: var(--ink);
    font-style: normal;
    text-align: right;
    line-height: 1.35;
  }
  .address svg { width: 16px; height: 20px; flex: none; }
</style>
</head>
<body>
<main class="sheet">

  <section class="card card--back" aria-label="Card back">
    <svg class="card__shapes" viewBox="0 0 660 377" aria-hidden="true">
      <polygon points="0,345 322,345 316,377 0,377" fill="var(--orange)"/>
      <polygon points="330,345 660,345 660,377 324,377" fill="var(--cyan)"/>
    </svg>
    <div class="brand">
      <span class="brand__line">Marsh Building</span>
      <span class="brand__line brand__line--sub">&amp; Construction</span>
    </div>
  </section>

  <section class="card card--front" aria-label="Card front">
    <svg class="card__shapes" viewBox="0 0 660 377" aria-hidden="true">
      <polygon points="0,205 320,205 294,377 0,377" fill="var(--orange)"/>
      <polygon points="328,205 660,205 660,377 302,377" fill="var(--cyan)"/>
    </svg>
    <div class="brand">
      <span class="brand__line">Marsh Building</span>
      <span class="brand__line brand__line--sub">&amp; Construction</span>
    </div>
    <div class="person">
      <h1 class="person__name">Liam Porter</h1>
      <p class="person__role">Construction Manager</p>
    </div>
    <ul class="contacts">
      <li>
        <svg viewBox="0 0 16 16" aria-hidden="true"><rect x="4" y="1" width="8" height="14" rx="1.5" fill="none" stroke="#111" stroke-width="1.6"/><line x1="6" y1="12" x2="10" y2="12" stroke="#111" stroke-width="1.4"/></svg>
        <span>0400 213 594</span>
      </li>
      <li>
        <svg viewBox="0 0 16 16" aria-hidden="true"><rect x="1" y="3" width="14" height="10" fill="#111"/><polyline points="1,3 8,9 15,3" fill="none" stroke="#fff" stroke-width="1.2"/></svg>
        <span>Liam@marshbuilding.com.au</span>
      </li>
    </ul>
    <address class="address">
      <span>14 Tarrant Rise<br>Harbourvale WA 6299</span>
      <svg viewBox="0 0 16 20" aria-hidden="true"><path d="M8 1a6 6 0 0 0-6 6c0 4.5 6 12 6 12s6-7.5 6-12a6 6 0 0 0-6-6z" fill="#111"/><circle cx="8" cy="7" r="2.2" fill="var(--cyan)"/></svg>
    </address>
  </section>

</main>
</body>
</html>
```